Professional looking Roller Blind Discount Card that portrays quality at a value for money price!

We need a double sided business card designed as a discount card. Size 90mm wide x 55mm high.We would like it to look professional and portray quality at a value for money price point.I have uploaded a word document with a basic layout with the information we want included on each side of the card. Please put your own thought into the layout.

Contact Information for Business Card

As per word document attached.

```html
<!DOCTYPE html>
<html lang="en">
<head>
<meta charset="utf-8">
<title>Roller Blinds Discount Card</title>
<link href="https://fonts.googleapis.com/css2?family=Poppins:wght@400;500;600;700&family=Oswald:wght@500;700&family=Great+Vibes&display=swap" rel="stylesheet">
<style>
  :root {
    --brand-blue: #1fa3dd;
    --brand-blue-dark: #1283c4;
    --brand-blue-light: #6fd0f5;
    --ink: #3d3d3d;
    --card: #ffffff;
    --backdrop: #e9ecef;
  }
  * { margin: 0; padding: 0; box-sizing: border-box; }
  html, body { width: 1200px; height: 874px; overflow: hidden; }
  body {
    background: var(--backdrop);
    font-family: "Poppins", sans-serif;
    color: var(--ink);
    display: flex;
    flex-direction: column;
    align-items: center;
    justify-content: center;
    gap: 32px;
  }
  .card {
    position: relative;
    width: 660px;
    height: 403px;
    background: var(--card);
    box-shadow: 0 4px 18px rgba(0,0,0,0.12);
    overflow: hidden;
  }

  /* Front side */
  .front-title {
    position: absolute; left: 26px; top: 4px;
    font-weight: 700; font-size: 74px; letter-spacing: -1px;
    color: var(--brand-blue); line-height: 1.1;
  }
  .front-subtitle {
    position: absolute; left: 28px; top: 90px;
    font-weight: 500; font-size: 29px; line-height: 1;
  }
  .photo-frame {
    position: absolute; left: 26px; top: 138px;
    width: 400px; height: 236px; border-radius: 18px; overflow: hidden;
  }
  .photo-area {
    width: 100%; height: 100%;
    background: linear-gradient(120deg, #6b5548 0%, #7d8d62 35%, #a9c59a 60%, #dfe6dc 100%);
  }
  .call-band {
    position: absolute; left: 0; right: 0; bottom: 0; height: 52px;
    background: var(--brand-blue);
    color: #fff; font-size: 23px; font-weight: 400;
    display: flex; align-items: center; justify-content: center; gap: 8px;
  }
  .call-band strong { font-weight: 700; }
  .fabric-bubble {
    position: absolute; left: 448px; top: 196px; width: 186px; height: 110px;
  }
  .fabric-bubble span {
    position: absolute; inset: 8px 10px 26px 10px;
    display: flex; align-items: center; justify-content: center; text-align: center;
    font-family: "Great Vibes", cursive; color: #fff; font-size: 24px; line-height: 0.95;
  }
  .brand-name {
    position: absolute; left: 448px; top: 322px; width: 190px;
    display: flex; align-items: center; gap: 8px;
    font-weight: 600; font-size: 19px; color: var(--brand-blue-dark);
  }
  .brand-name i {
    display: block; width: 14px; height: 14px; background: var(--brand-blue-dark);
  }

  /* Back side */
  .discount {
    position: absolute; left: 24px; top: 14px;
    font-weight: 700; font-size: 70px; line-height: 0.86;
    color: var(--brand-blue); letter-spacing: -2px;
  }
  .offer-headline {
    position: absolute; left: 200px; top: 22px;
    font-weight: 500; font-size: 39px; line-height: 1.02; letter-spacing: -0.5px;
  }
  .blind-types {
    position: absolute; left: 200px; top: 108px;
    font-size: 25px; font-weight: 400;
  }
  .blind-types b { color: var(--brand-blue); font-size: 18px; margin: 0 4px; }
  .badges {
    position: absolute; left: 26px; top: 168px;
    display: flex; gap: 34px;
  }
  .badge { position: relative; width: 168px; height: 168px; }
  .badge svg { position: absolute; inset: 0; }
  .badge-text {
    position: absolute; inset: 0;
    display: flex; flex-direction: column; align-items: center; justify-content: center;
    color: #fff; font-family: "Oswald", sans-serif; text-align: center;
  }
  .badge-text strong { font-size: 46px; font-weight: 700; line-height: 1; }
  .badge-text small { font-size: 11px; font-weight: 500; letter-spacing: 0.3px; margin-top: 2px; }
  .back-call {
    position: absolute; left: 28px; bottom: 16px;
    font-size: 31px; font-weight: 400;
  }
  .back-call strong { color: var(--brand-blue); font-weight: 600; }
</style>
</head>
<body>

<section class="card card-front">
  <h1 class="front-title">ROLLER BLINDS</h1>
  <p class="front-subtitle">FREE in Home Meacure &amp; Quote</p>
  <div class="photo-frame">
    <div class="photo-area" role="img" aria-label="Room with roller blinds over windows looking onto a leafy garden"></div>
    <div class="call-band">CALL <strong>0400 555 210</strong> TODAY!</div>
  </div>
  <div class="fabric-bubble">
    <svg width="186" height="110" viewBox="0 0 186 110">
      <defs>
        <linearGradient id="bubbleFill" x1="0" y1="0" x2="0" y2="1">
          <stop offset="0" stop-color="#6fd0f5"/>
          <stop offset="1" stop-color="#1283c4"/>
        </linearGradient>
      </defs>
      <ellipse cx="93" cy="44" rx="90" ry="41" fill="url(#bubbleFill)"/>
      <path d="M112 78 L124 108 L140 72 Z" fill="#1283c4"/>
    </svg>
    <span>Huge Selection<br>of Fabrics</span>
  </div>
  <div class="brand-name"><i></i>Brightvale Interiors</div>
</section>

<section class="card card-back">
  <div class="discount">25%<br>OFF</div>
  <h2 class="offer-headline">QUALITY CUSTOM<br>MADE ROLLER BLINDS</h2>
  <p class="blind-types">Blockout<b>•</b>screen<b>•</b>LightFiltering</p>

  <svg width="0" height="0" style="position:absolute">
    <defs>
      <radialGradient id="sealFill" cx="0.4" cy="0.3" r="0.8">
        <stop offset="0" stop-color="#8fdcf8"/>
        <stop offset="0.55" stop-color="#2aa6e0"/>
        <stop offset="1" stop-color="#1277bb"/>
      </radialGradient>
    </defs>
  </svg>

  <div class="badges">
    <div class="badge">
      <svg viewBox="0 0 168 168"><circle cx="84" cy="84" r="76" fill="url(#sealFill)" stroke="#1d8fd0" stroke-width="10" stroke-dasharray="5 4"/><circle cx="84" cy="84" r="62" fill="none" stroke="#fff" stroke-opacity="0.35" stroke-width="1.5"/></svg>
      <div class="badge-text"><strong>FREE</strong><small>IN HOME MEASURE &amp; QUOTE</small></div>
    </div>
    <div class="badge">
      <svg viewBox="0 0 168 168"><circle cx="84" cy="84" r="76" fill="url(#sealFill)" stroke="#1d8fd0" stroke-width="10" stroke-dasharray="5 4"/><circle cx="84" cy="84" r="62" fill="none" stroke="#fff" stroke-opacity="0.35" stroke-width="1.5"/></svg>
      <div class="badge-text"><strong>BEST</strong><small>PRICE GUARANTEE</small></div>
    </div>
    <div class="badge">
      <svg viewBox="0 0 168 168"><circle cx="84" cy="84" r="76" fill="url(#sealFill)" stroke="#1d8fd0" stroke-width="10" stroke-dasharray="5 4"/><circle cx="84" cy="84" r="62" fill="none" stroke="#fff" stroke-opacity="0.35" stroke-width="1.5"/></svg>
      <div class="badge-text"><strong>FAMILY</strong><small>OWNED &amp; OPERATED</small></div>
    </div>
  </div>

  <p class="back-call">CALL <strong>0400 555 210</strong> TODAY!</p>
</section>

</body>
</html>
```